Coastline Premier Retreats Business Card Design

Design a business card for Coastline Premier Retreats. Look at the website for colors and reference. Card should have logo, name, title, office number, mobile number, email, URL and a tagline like, "Luxury Hotel & Resort Email Marketing" (This might change).

https://www.coastlinepremierretreats.example

The rest I will leave up to your imagination.

Contact Information for Business Card

Logo, name, title, office number, mobile number, email, URL and a tagline like, "Luxury Hotel & Resort Email Marketing" (This might change).

```html
<!DOCTYPE html>
<html lang="en">
<head>
<meta charset="utf-8">
<title>Coastline Premier Retreats – Business Card</title>
<link href="https://fonts.googleapis.com/css2?family=Montserrat:wght@400;500;700;800&display=swap" rel="stylesheet">
<style>
  :root {
    --backdrop: #2b2b2b;
    --card: #1c1c1c;
    --orange: #f07a12;
    --white: #f4f4f4;
    --muted: #2a2a2a;
  }
  * { box-sizing: border-box; margin: 0; padding: 0; }
  html, body {
    width: 1200px; height: 900px; overflow: hidden;
    background: var(--backdrop);
    font-family: "Montserrat", sans-serif;
  }
  .stage {
    width: 1200px; height: 900px;
    display: flex; flex-direction: column; align-items: center; justify-content: center;
    gap: 44px;
  }
  .card {
    position: relative;
    width: 660px; height: 377px;
    background: var(--card);
    border-bottom: 4px solid var(--orange);
    box-shadow: 0 10px 24px rgba(0,0,0,.45);
  }

  /* Back side */
  .card-back { display: flex; align-items: center; justify-content: center; }
  .back-brand {
    display: flex; align-items: center; gap: 18px;
    font-weight: 800; font-size: 34px; letter-spacing: 2px; text-transform: uppercase;
    color: var(--muted);
  }
  .back-brand .mark { width: 26px; height: 26px; background: var(--muted); }

  /* Front side */
  .holder {
    position: absolute; top: 42px; right: 62px; text-align: right;
  }
  .holder-name {
    font-weight: 800; font-size: 30px; letter-spacing: 1px; color: var(--orange); text-transform: uppercase;
  }
  .holder-title { font-size: 15px; color: var(--white); margin-top: 2px; }
  .accent-bar {
    position: absolute; top: 40px; right: 0; width: 34px; height: 40px; background: var(--orange);
  }
  .brand {
    position: absolute; left: 44px; top: 168px;
    display: flex; align-items: center; gap: 10px;
    font-weight: 700; font-size: 19px; letter-spacing: 1px; color: var(--white); text-transform: uppercase;
  }
  .brand .mark { width: 14px; height: 14px; background: var(--orange); }
  .address {
    position: absolute; left: 44px; top: 220px;
    font-size: 13.5px; line-height: 1.35; color: var(--white);
  }
  .contacts {
    position: absolute; left: 44px; top: 272px; list-style: none;
    font-size: 13.5px; line-height: 1.5; color: var(--white);
  }
  .contacts li { display: flex; align-items: center; gap: 9px; }
  .contacts svg { width: 12px; height: 12px; flex: none; }
  .tagline {
    position: absolute; right: 36px; bottom: 60px; text-align: right;
    font-size: 15px; line-height: 1.3; color: var(--orange);
  }
</style>
</head>
<body>
<main class="stage">
  <section class="card card-back" aria-label="Card back">
    <div class="back-brand"><span class="mark"></span>Coastline Premier Retreats</div>
  </section>

  <section class="card card-front" aria-label="Card front">
    <span class="accent-bar"></span>
    <div class="holder">
      <p class="holder-name">Daniel Reyes</p>
      <p class="holder-title">CEO/Founder</p>
    </div>

    <div class="brand"><span class="mark"></span>Coastline Premier Retreats</div>

    <p class="address">Po Box, 48 Harbor Lane<br>Seaside Bay, CA 90000</p>

    <ul class="contacts">
      <li>
        <svg viewBox="0 0 12 12" aria-hidden="true"><rect x="3" y="0.5" width="6" height="11" rx="1" fill="none" stroke="var(--orange)" stroke-width="1.2"/><circle cx="6" cy="9.6" r=".7" fill="var(--orange)"/></svg>
        555.014.2200
      </li>
      <li>
        <svg viewBox="0 0 12 12" aria-hidden="true"><path d="M1 4 Q6 0 11 4 L10 5.5 L8 4.6 L8 3.6 Q6 3 4 3.6 L4 4.6 L2 5.5 Z" fill="var(--orange)"/><rect x="2.5" y="6" width="7" height="5" rx="1" fill="var(--orange)"/></svg>
        +34 600 000 127
      </li>
      <li>
        <svg viewBox="0 0 12 12" aria-hidden="true"><rect x="0.6" y="2.5" width="10.8" height="7.5" fill="none" stroke="var(--orange)" stroke-width="1.2"/><path d="M0.6 2.5 L6 7 L11.4 2.5" fill="none" stroke="var(--orange)" stroke-width="1.2"/></svg>
        info@coastlinepremierretreats.example
      </li>
      <li>
        <svg viewBox="0 0 12 12" aria-hidden="true"><circle cx="6" cy="6" r="5.2" fill="none" stroke="var(--orange)" stroke-width="1.2"/><path d="M0.8 6 H11.2 M6 0.8 Q2.8 6 6 11.2 M6 0.8 Q9.2 6 6 11.2" fill="none" stroke="var(--orange)" stroke-width="1"/></svg>
        www.coastlinepremierretreats.example
      </li>
    </ul>

    <p class="tagline">Luxury Hotel &amp; Resort<br>Email Marketing</p>
  </section>
</main>
</body>
</html>
```